KORVAL:advise Business Cards

We need a business card design for KORVAL:advise (Logo Attached), a management consultancy specialized in brand & business building.

Design should be clean, smart and a touch of innnovation without being gimmicky.

The details on the card should be:
Name: Tomas Velduren
Title: Managing Director
Address: 42 Marlowe Pier, Tarn Vessel Tower, Singapore 073926
Tel: +6285927461082
email: tv@korvaladvise.example
website: korvaladvise.example

For further background on corporate identity, please check www.korvaladvise.example
Updates

Dear all,

Many thanks for the submissions so far! I gave feedback to those designs that I prefer at this stage.

Overall I see that my preference goes into the direction that 'less is more' and 'simple is beautiful'

Please create uniqueness and standout by the simplicity and attraction of the overall concept and design.

Many thanks and please shout incase of questions!

Tomas

Industry/Entity Type

Business

```html
<!DOCTYPE html>
<html lang="en">
<head>
<meta charset="utf-8">
<title>KORVAL:advise — Business Cards</title>
<link rel="stylesheet" href="https://fonts.googleapis.com/css2?family=Open+Sans:wght@400;600;700&display=swap">
<style>
  :root {
    --backdrop: #e6e4e1;
    --card-light: #ffffff;
    --card-dark: #4b4b4b;
    --ink: #3a3a3a;
    --ink-soft: #444444;
    --accent: #f07800;
    --rule: #8a8a8a;
    --white: #ffffff;
  }
  * { margin: 0; padding: 0; box-sizing: border-box; }
  html, body {
    width: 1200px; height: 1088px; overflow: hidden;
    background: var(--backdrop);
    font-family: "Open Sans", Arial, sans-serif;
  }
  .canvas { position: relative; width: 1200px; height: 1088px; }

  .card { position: absolute; }
  .card-front {
    left: 307px; top: 38px; width: 855px; height: 487px;
    background: var(--card-light);
    box-shadow: 0 2px 6px rgba(0,0,0,.18);
  }
  .card-back {
    left: 30px; top: 556px; width: 856px; height: 489px;
    background: var(--card-dark);
    box-shadow: 0 2px 6px rgba(0,0,0,.22);
  }

  .wordmark {
    position: absolute; white-space: nowrap;
    font-weight: 600; letter-spacing: -0.5px; line-height: 1;
  }
  .card-front .wordmark {
    left: 0; right: 0; top: 74px; text-align: center;
    font-size: 64px; color: var(--ink-soft);
  }
  .card-back .wordmark {
    left: 0; right: 0; top: 206px; text-align: center;
    font-size: 74px; color: var(--white);
  }

  .divider {
    position: absolute; left: 0; right: 0; top: 274px; height: 4px;
    background: linear-gradient(90deg, rgba(138,138,138,0) 0%, rgba(138,138,138,.45) 25%, var(--rule) 60%, #7a7a7a 100%);
  }

  .person { position: absolute; right: 21px; top: 236px; text-align: right; }
  .person-name { font-size: 25px; font-weight: 700; color: var(--ink-soft); line-height: 1; }
  .person-title { margin-top: 22px; font-size: 20px; color: var(--accent); line-height: 1; }

  .contacts {
    position: absolute; right: 44px; top: 351px;
    list-style: none; text-align: right;
  }
  .contacts li {
    display: flex; justify-content: flex-end; align-items: center;
    gap: 8px; height: 37px;
    font-size: 21px; color: var(--ink);
  }
  .contacts svg { width: 18px; height: 18px; flex: none; }

  .address {
    position: absolute; left: 47px; top: 396px;
    font-size: 21px; line-height: 33px; color: var(--ink); font-style: normal;
  }

  .back-url {
    position: absolute; left: 0; right: 0; top: 376px; text-align: center;
    font-size: 22px; letter-spacing: 4px; color: var(--white);
  }
</style>
</head>
<body>
<main class="canvas">

  <section class="card card-front" aria-label="Business card front">
    <div class="wordmark">KORVAL:advise</div>
    <div class="divider"></div>
    <div class="person">
      <p class="person-name">Tomas Velduren</p>
      <p class="person-title">Managing Director</p>
    </div>
    <ul class="contacts">
      <li>
        <svg viewBox="0 0 18 18" aria-hidden="true">
          <circle cx="9" cy="9" r="8" fill="none" stroke="var(--accent)" stroke-width="1.6"/>
          <path d="M6.2 4.6 L7.8 6.8 L6.9 7.8 Q7.8 10 10.2 11.1 L11.2 10.2 L13.4 11.8 L12.4 13.3 Q7.2 12.6 4.7 5.6 Z" fill="var(--accent)"/>
        </svg>
        <span>+6285927461082</span>
      </li>
      <li>
        <svg viewBox="0 0 18 18" aria-hidden="true">
          <rect x="1.5" y="4" width="15" height="11" rx="1.5" fill="var(--accent)"/>
          <path d="M2.5 5.5 L9 10.5 L15.5 5.5" fill="none" stroke="var(--white)" stroke-width="1.5"/>
        </svg>
        <span>tv@korvaladvise.example</span>
      </li>
      <li>
        <svg viewBox="0 0 18 18" aria-hidden="true">
          <circle cx="9" cy="9" r="7.5" fill="none" stroke="var(--accent)" stroke-width="1.6"/>
          <ellipse cx="9" cy="9" rx="3.2" ry="7.5" fill="none" stroke="var(--accent)" stroke-width="1.3"/>
          <path d="M1.5 9 H16.5 M3 5.2 H15 M3 12.8 H15" stroke="var(--accent)" stroke-width="1.2"/>
        </svg>
        <span>www.korvaladvise.example</span>
      </li>
    </ul>
    <address class="address">
      42 Marlowe Pier, Tarn<br>
      Vessel Tower, Singapore 073926
    </address>
  </section>

  <section class="card card-back" aria-label="Business card back">
    <div class="wordmark">KORVAL:advise</div>
    <p class="back-url">www.korvaladvise.example</p>
  </section>

</main>
</body>
</html>
```